Vantiqo custom business card design

Need a authentic, innovative business card design for a new mobile app business. I am uploading a few screen images from our app for you to view. I would like app design theme to match business card design. I can also send logo images.

```html
<!DOCTYPE html>
<html lang="en">
<head>
<meta charset="utf-8">
<title>Vantiqo Business Card</title>
<link rel="stylesheet" href="https://fonts.googleapis.com/css2?family=Open+Sans:wght@400;600;700;800&display=swap">
<style>
  :root {
    --purple: #5e0a8c;
    --purple-deep: #4f0677;
    --ink: #1c1c1c;
    --text: #3a3a3a;
    --paper: #ffffff;
    --stage: #d9d9dc;
  }
  * { box-sizing: border-box; margin: 0; padding: 0; }
  html, body { width: 1200px; height: 1000px; overflow: hidden; }
  body {
    background: var(--stage);
    font-family: "Open Sans", sans-serif;
    position: relative;
  }
  .card {
    position: absolute;
    left: 250px;
    width: 700px;
    height: 400px;
    border-radius: 22px;
    overflow: hidden;
  }
  /* Back side */
  .card-back {
    top: 60px;
    background: linear-gradient(120deg, var(--purple) 0%, var(--purple) 55%, var(--purple-deep) 100%);
  }
  .back-mark {
    position: absolute;
    left: 50%; top: 150px;
    transform: translate(-50%, -50%);
    display: flex; align-items: center; gap: 18px;
  }
  .back-mark .dot {
    width: 52px; height: 52px; border-radius: 50%;
    background: var(--paper);
  }
  .back-mark .name {
    font-weight: 800; font-size: 60px; color: var(--paper); letter-spacing: 0.5px;
  }
  .back-url {
    position: absolute; left: 0; right: 0; top: 285px;
    text-align: center; color: var(--paper);
    font-size: 20px; letter-spacing: 7px;
  }
  /* Front side */
  .card-front {
    top: 540px;
    background: linear-gradient(160deg, #ffffff 0%, #ffffff 60%, #ededed 100%);
  }
  .identity { position: absolute; left: 48px; top: 70px; }
  .identity .person {
    color: var(--purple); font-weight: 700; font-size: 27px; line-height: 1;
  }
  .identity .role {
    color: var(--ink); font-size: 17px; margin-top: 4px; letter-spacing: 0.3px;
  }
  .divider {
    position: absolute; left: 48px; right: 48px; top: 148px;
    height: 2px; background: var(--ink);
  }
  .contacts {
    position: absolute; left: 48px; top: 164px;
    list-style: none;
  }
  .contacts li {
    display: flex; align-items: center; gap: 12px;
    font-size: 18px; color: var(--text); line-height: 27px;
  }
  .contacts svg { width: 20px; height: 20px; fill: var(--purple); flex: none; }
  .brand {
    position: absolute; right: 48px; top: 52px;
    display: flex; align-items: center; gap: 12px;
  }
  .brand .dot {
    width: 34px; height: 34px; border-radius: 50%; background: var(--purple);
  }
  .brand .name {
    font-weight: 800; font-size: 40px; color: var(--ink);
  }
  .address {
    position: absolute; right: 48px; top: 210px;
    text-align: right; font-size: 19px; color: var(--text); line-height: 27px;
  }
  .address .web { letter-spacing: 2px; }
  .band {
    position: absolute; left: 0; right: 0; bottom: 0; height: 26px;
  }
</style>
</head>
<body>
  <section class="card card-back" aria-label="Card back">
    <div class="back-mark">
      <span class="dot"></span>
      <span class="name">Vantiqo</span>
    </div>
    <p class="back-url">vantiqo.com</p>
  </section>

  <section class="card card-front" aria-label="Card front">
    <div class="identity">
      <h1 class="person">MARCUS HALE</h1>
      <p class="role">PRESIDENT</p>
    </div>

    <div class="brand">
      <span class="dot"></span>
      <span class="name">Vantiqo</span>
    </div>

    <div class="divider"></div>

    <ul class="contacts">
      <li>
        <svg viewBox="0 0 20 20" aria-hidden="true"><path d="M2 6c0-2 3-3 8-3s8 1 8 3v2h-4V6.5H6V8H2z"/><path d="M4 9h12l1 8H3z"/></svg>
        412 5068 3170
      </li>
      <li>
        <svg viewBox="0 0 20 20" aria-hidden="true"><path d="M6 1h8a1 1 0 0 1 1 1v16a1 1 0 0 1-1 1H6a1 1 0 0 1-1-1V2a1 1 0 0 1 1-1zm1 2v12h6V3z"/></svg>
        719 2684 4021
      </li>
      <li>
        <svg viewBox="0 0 20 20" aria-hidden="true"><path d="M5 2h8l2 2v4H5z"/><path d="M2 9h16v9H2z"/></svg>
        630 5147 2298
      </li>
      <li>
        <svg viewBox="0 0 20 20" aria-hidden="true"><path d="M1 4h18v12H1zm2 2v.5l7 5 7-5V6l-7 5z"/></svg>
        marcus@vantiqo.com
      </li>
    </ul>

    <address class="address" style="font-style:normal">
      4127 Linden Crest Road<br>
      Maple Falls, NY 11020<br>
      <span class="web">www.vantiqo.com</span>
    </address>

    <svg class="band" viewBox="0 0 700 26" preserveAspectRatio="none" aria-hidden="true">
      <polygon points="0,0 520,0 505,26 0,26" fill="var(--purple)"/>
      <polygon points="524,0 700,0 700,26 509,26" fill="var(--ink)"/>
    </svg>
  </section>
</body>
</html>
```